Business Card for Industrial Distributor

We need a business card design for an industrial distributor. We sell machine parts for the manufacturing and oil industry. We would like the cards to look clean and modern but with a touch of industry.

Our colors are blue/white.

Please feel free to visit our website www.korvelpartsco.com

Target Market(s)

mexican manufacturers in the automobile/aerospace industry

Industry/Entity Type

Industrial

Colors
ffffff
0555a3

```html
<!DOCTYPE html>
<html lang="en">
<head>
<meta charset="utf-8">
<title>Korvel Business Card</title>
<link href="https://fonts.googleapis.com/css2?family=Lato:wght@400;700;900&display=swap" rel="stylesheet">
<style>
  :root {
    --brand-blue: #0555a3;
    --card-blue: #135ba3;
    --light-blue: #2f7bc4;
    --white: #ffffff;
    --text-grey: #6b6b6b;
    --backdrop: #3b3b3b;
  }
  * { margin: 0; padding: 0; box-sizing: border-box; }
  html, body { width: 1200px; height: 810px; overflow: hidden; }
  body {
    background: var(--backdrop);
    font-family: "Lato", Arial, sans-serif;
    position: relative;
  }
  .card {
    position: absolute;
    width: 525px;
    height: 300px;
    overflow: hidden;
    box-shadow: 0 6px 18px rgba(0,0,0,.35);
  }
  .card-front { left: 80px; top: 80px; background: var(--card-blue); }
  .card-back { left: 595px; top: 430px; background: var(--white); }

  .brand {
    position: absolute;
    display: flex;
    align-items: center;
    gap: 12px;
    font-weight: 900;
    letter-spacing: 1px;
  }
  .brand-dot { border-radius: 50%; flex: none; }

  .card-front .brand { left: 50%; top: 108px; transform: translateX(-50%); color: var(--white); font-size: 58px; }
  .card-front .brand-dot { width: 44px; height: 44px; background: var(--white); }
  .card-front .site {
    position: absolute; left: 0; right: 0; top: 226px;
    text-align: center; color: var(--white); font-size: 13px; letter-spacing: .3px;
  }

  .card-back .brand { left: 34px; top: 118px; color: var(--brand-blue); font-size: 44px; }
  .card-back .brand-dot { width: 34px; height: 34px; background: var(--brand-blue); }
  .divider {
    position: absolute; left: 262px; top: 40px; width: 1px; height: 150px;
    background: var(--brand-blue);
  }
  .contact { position: absolute; left: 280px; top: 38px; color: var(--text-grey); }
  .person-name { color: var(--brand-blue); font-size: 20px; font-weight: 700; line-height: 1; }
  .person-role { font-size: 11px; margin-top: 3px; }
  .address { font-size: 12.5px; line-height: 1.35; margin-top: 18px; }
  .lines { list-style: none; margin-top: 12px; font-size: 12.5px; line-height: 1.4; }
  .lines li { display: flex; align-items: center; gap: 7px; }
  .lines svg { width: 12px; height: 12px; fill: var(--brand-blue); flex: none; }
  .card-back .site {
    position: absolute; left: 258px; top: 204px; font-size: 12.5px; line-height: 1.2; color: var(--text-grey);
    z-index: 2;
  }
  .card-back .site strong { color: var(--brand-blue); font-weight: 400; }
  .swoosh { position: absolute; left: 0; bottom: 0; width: 525px; height: 90px; z-index: 1; }
</style>
</head>
<body>

<section class="card card-front">
  <div class="brand"><span class="brand-dot"></span><span>Korvel</span></div>
  <p class="site">www.korvelpartsco.com</p>
</section>

<section class="card card-back">
  <div class="brand"><span class="brand-dot"></span><span>Korvel</span></div>
  <div class="divider"></div>
  <div class="contact">
    <p class="person-name">Daniel Reyes</p>
    <p class="person-role">President &amp; CEO</p>
    <p class="address">4820 Harbor Mill Rd,<br>Laredo, TX 78041</p>
    <ul class="lines">
      <li><svg viewBox="0 0 12 12"><path d="M3 1l2 2.5-1.2 1.3a6 6 0 0 0 3.4 3.4L8.5 7 11 9l-1.5 2C5 11 1 7 1 2.5z"/></svg>(555) 310 - 4420</li>
      <li><svg viewBox="0 0 12 12"><path d="M3 1h5v3H3zM1 5h10v5H9v1H3v-1H1zm3 3v2h4V8z"/></svg>(555) 310 - 4427</li>
      <li><svg viewBox="0 0 12 12"><path d="M1 3h10v6H1zm1 .8v.3L6 7l4-2.9v-.3z"/></svg>sales@korvelpartsco.com</li>
    </ul>
  </div>
  <p class="site">www.<strong>korvelpartsco</strong>.com</p>
  <svg class="swoosh" viewBox="0 0 525 90" preserveAspectRatio="none" aria-hidden="true">
    <path d="M0 90 L0 72 Q300 66 525 14 L525 90 Z" fill="var(--brand-blue)"/>
    <path d="M0 62 Q300 56 525 2 L525 8 Q300 62 0 67 Z" fill="var(--light-blue)"/>
  </svg>
</section>

</body>
</html>
```